Dunmore Roofing

Want a professional looking business card

Industry/Entity Type

Business

Contact Information for Business Card

Paul Dunmore ( Owner) paul@dunmoreroofing-example.com, www.dunmoreroofing-example.com, Adress: 4172 Township road 43 Elmbrook,ON K9X4T2

```html
<!DOCTYPE html>
<html lang="en">
<head>
<meta charset="utf-8">
<title>Dunmore Roofing – Business Card</title>
<link rel="stylesheet" href="https://fonts.googleapis.com/css2?family=Roboto:wght@400;700&family=Roboto+Condensed:wght@500&display=swap">
<style>
  :root {
    --backdrop: #2a2a2a;
    --card-white: #f3f3f3;
    --brand-blue: #1b4788;
    --accent-grey: #8a8a8a;
    --back-grey-light: #858585;
    --back-grey-dark: #6e6e6e;
    --text-light: #ffffff;
  }
  * { margin: 0; padding: 0; box-sizing: border-box; }
  html, body { width: 1200px; height: 960px; overflow: hidden; background: var(--backdrop); }
  .canvas { position: relative; width: 1200px; height: 960px; font-family: "Roboto", Arial, sans-serif; }

  .card { position: absolute; width: 600px; height: 343px; overflow: hidden; }
  .card-front { left: 314px; top: 113px; background: var(--card-white); }
  .card-back {
    left: 311px; top: 472px;
    background: radial-gradient(ellipse at 50% 35%, var(--back-grey-light), var(--back-grey-dark));
    color: var(--text-light);
  }

  .front-band { position: absolute; left: 0; top: 0; width: 600px; height: 343px; }

  .brand-name {
    position: absolute; font-family: "Roboto", Arial, sans-serif; font-weight: 700;
    letter-spacing: 2px; white-space: nowrap;
  }
  .card-front .brand-name { right: 42px; top: 118px; font-size: 27px; color: var(--brand-blue); }
  .card-back .brand-name { left: 0; right: 0; top: 158px; text-align: center; font-size: 40px; color: var(--text-light); }

  .holder { position: absolute; left: 31px; top: 202px; color: var(--text-light); }
  .holder-name { font-family: "Roboto Condensed", Arial, sans-serif; font-weight: 500; font-size: 21px; line-height: 26px; }
  .holder-role { font-size: 14px; line-height: 18px; margin-top: 1px; }

  .contact-list { position: absolute; left: 31px; top: 262px; list-style: none; color: var(--text-light); font-size: 14px; }
  .contact-list li { display: flex; align-items: center; height: 19.5px; }
  .contact-list svg { width: 12px; height: 12px; margin-right: 11px; fill: var(--text-light); }

  .address { position: absolute; right: 42px; top: 282px; text-align: right; color: var(--text-light); font-size: 14px; line-height: 19.5px; }

  .back-web {
    position: absolute; left: 0; right: 0; top: 285px; text-align: center;
    font-size: 14px; letter-spacing: 3.6px; color: var(--text-light);
  }
</style>
</head>
<body>
<main class="canvas">

  <section class="card card-front" aria-label="Business card front">
    <svg class="front-band" viewBox="0 0 600 343" aria-hidden="true">
      <polygon points="220,187 236,187 264,215 600,215 600,221 258,221" fill="var(--accent-grey)"/>
      <polygon points="0,187 214,187 252,225 600,225 600,343 0,343" fill="var(--brand-blue)"/>
    </svg>

    <div class="brand-name">DUNMORE ROOFING</div>

    <div class="holder">
      <div class="holder-name">PAUL DUNMORE</div>
      <div class="holder-role">OWNER</div>
    </div>

    <ul class="contact-list">
      <li>
        <svg viewBox="0 0 24 24"><path d="M6.6 10.8a15 15 0 0 0 6.6 6.6l2.2-2.2c.3-.3.7-.4 1-.2 1.1.4 2.3.6 3.6.6.6 0 1 .4 1 1V20c0 .6-.4 1-1 1A17 17 0 0 1 3 4c0-.6.4-1 1-1h3.5c.6 0 1 .4 1 1 0 1.3.2 2.5.6 3.6.1.3 0 .7-.2 1z"/></svg>
        555 014 2738
      </li>
      <li>
        <svg viewBox="0 0 24 24"><path d="M2 5h20v14H2z M3 6l9 7 9-7" fill="none" stroke="#fff" stroke-width="2"/></svg>
        paul@dunmoreroofing-example.com
      </li>
      <li>
        <svg viewBox="0 0 24 24"><circle cx="12" cy="12" r="10" fill="none" stroke="#fff" stroke-width="2"/><path d="M2 12h20M12 2c3 3 3 17 0 20M12 2c-3 3-3 17 0 20" fill="none" stroke="#fff" stroke-width="2"/></svg>
        www.dunmoreroofing-example.com
      </li>
    </ul>

    <div class="address">
      4172 Township road 43<br>
      Elmbrook, ON K9X4T2
    </div>
  </section>

  <section class="card card-back" aria-label="Business card back">
    <div class="brand-name">DUNMORE ROOFING</div>
    <div class="back-web">www.dunmoreroofing-example.com</div>
  </section>

</main>
</body>
</html>
```